Website Design for Chef Wen Chinese Restaurant

Chef Wen is a new Chinese Restaurant. It offers exceptional dining experience with authentic and dynamic dishes created with quality ingredients.

A vivid website theme is required to promote this new restaurant online. Logo, menu, wine list and a few other files are attached for help with designing.

A very rough demo website has been setup and can be accessed via http://www.chefwen.com.au. It is for telling designers what content is shown up on each page (except for homepage). By reading the about us page, designers can get some more info of Chef Wen. However, the layout, theme color, font, etc are not set in stone. Visitors should be able to feel Chef Wen restaurant's authentic Chinese cuisine and high hygiene standard. Home page of the website could be The "Our website is coming soon" description is shown on demo site but do not required to be presented on new design.

Some main pages design should be included: Home (landing page), About us, Menu (Dishes), Winelist, Gallery, Contact us. No HTML and coding required. The output should be well layered psd or png files with acceptable resolution for web use.

A few other website can be referred to are:

http://larkspurasian.com.au/
http://www.river-lamp.com/
http://tamworthy.com.au/
http://harbelrestaurant.com.au/
http://www.quillerestaurant.com.au/
http://www.thekiln.com.au/

Industry/Entity Type

Restaurant

Requirements
Nice to have
• I expect designs of at least these webpages: homepage, menu page and contact us page. If you can provide "about us" page as well, it will probably help you win the competition. well layered psd or png file is my preference.
Should not have
• You don't have to make html/cs/js or any coding. All I need is just art design

```html
<!DOCTYPE html>
<html lang="en">
<head>
<meta charset="utf-8">
<title>Chef Wen Chinese Restaurant</title>
<link href="https://fonts.googleapis.com/css2?family=Arimo:wght@400;700&display=swap" rel="stylesheet">
<style>
:root{
  --page-bg:#fdfbc9;
  --red:#e50000;
  --red-dark:#b80000;
  --white:#ffffff;
  --ink:#111111;
  --panel-dark:#262626;
  --wood:#7a2a07;
  --cream:#fff6b8;
  --cream-soft:#fde9b0;
  --footer:#2a2a2a;
}
*{margin:0;padding:0;box-sizing:border-box}
html,body{width:1097px;height:1200px;overflow:hidden}
body{background:var(--page-bg);font-family:"Arimo",Arial,sans-serif;position:relative;color:var(--white)}
.brand{position:absolute;top:52px;left:0;width:1097px;text-align:center;display:flex;justify-content:center;align-items:center;gap:10px}
.brand-mark{width:16px;height:16px;background:var(--red)}
.brand-name{font-size:20px;font-weight:700;color:var(--ink);letter-spacing:.5px}
.main-nav{position:absolute;left:70px;top:153px;width:957px;height:48px;background:var(--red);border-radius:4px;box-shadow:0 0 0 1px var(--red-dark)}
.main-nav::before{content:"";position:absolute;inset:2px;border:1px solid var(--white);border-radius:3px}
.nav-flourish{position:absolute;top:18px;width:86px;height:12px;background:rgba(255,255,255,.55);border-radius:6px}
.nav-flourish.left{left:18px}.nav-flourish.right{right:18px}
.nav-links{position:absolute;top:0;left:0;height:48px;display:flex;align-items:center;list-style:none}
.nav-links li{position:absolute;font-size:18px;font-weight:700;white-space:nowrap}
.nav-links li.active{color:var(--ink)}
.hero{position:absolute;left:70px;top:220px;width:957px;height:286px;border-radius:5px;overflow:hidden;
  background:linear-gradient(90deg,#d9d5d0 0%,#e8e2dc 30%,#c8502a 55%,#b6361a 72%,#e2ddd6 100%)}
.hero-arrow{position:absolute;top:117px;width:38px;height:48px;background:rgba(30,30,30,.8);display:flex;align-items:center;justify-content:center}
.hero-arrow.prev{left:20px}.hero-arrow.next{right:20px}
.divider-flourish{position:absolute;left:506px;top:515px;width:85px;height:12px;background:var(--red);border-radius:6px;opacity:.85}
.welcome{position:absolute;left:70px;top:539px;width:652px;height:286px;border-radius:5px;
  background:linear-gradient(180deg,#1f1f1f,#3a3a3a 50%,#1c1c1c)}
.welcome h1{position:absolute;top:10px;left:0;width:100%;text-align:center;font-size:25px;font-weight:400;color:var(--cream);display:flex;justify-content:center;align-items:center;gap:8px}
.welcome p{position:absolute;left:33px;width:590px;font-size:12.5px;line-height:21px;color:#f2f2f2}
.welcome p.one{top:55px}.welcome p.two{top:160px}
.read-more{position:absolute;right:40px;top:246px;font-size:14px;font-weight:700;color:var(--cream);border-bottom:1px solid var(--cream);padding-bottom:2px}
.hours{position:absolute;left:741px;top:539px;width:286px;height:286px;border-radius:5px;
  background:linear-gradient(180deg,#6a2406,#8a3a10 50%,#5d1f05)}
.hours h2{position:absolute;top:10px;left:0;width:100%;text-align:center;font-size:25px;font-weight:400;color:var(--white);display:flex;justify-content:center;align-items:center;gap:7px}
.hours .tagline{position:absolute;left:11px;top:50px;font-size:20px;color:var(--cream)}
.hours dl{position:absolute;left:11px;top:95px;font-size:15px;line-height:21px}
.hours dt{font-weight:700;color:var(--white);font-size:16px}
.hours dd{color:var(--cream)}
.hours dd.gap{margin-bottom:20px}
.wine-band{position:absolute;left:70px;top:844px;width:957px;height:238px;border-radius:5px;background:var(--red);overflow:hidden}
.wine-photo{position:absolute;left:0;top:0;width:282px;height:238px;background:linear-gradient(90deg,#8c0c14 0%,#c4c0a0 60%,#d8d0a8 100%)}
.wine-col{position:absolute;top:30px;list-style:none}
.wine-col h3{font-size:20px;font-weight:400;color:var(--cream);margin-bottom:9px}
.wine-col li{font-size:15px;color:var(--cream-soft);height:28.5px}
.wine-col.red li{height:26px}
.wine-rule{position:absolute;top:20px;width:1px;height:210px;background:var(--cream-soft)}
.wine-rule::before,.wine-rule::after{content:"";position:absolute;left:-4px;width:9px;height:9px;border:1px solid var(--cream-soft);transform:rotate(45deg)}
.wine-rule::before{top:-2px}.wine-rule::after{bottom:-2px}
.site-footer{position:absolute;left:70px;top:1114px;width:957px;height:46px;background:var(--footer);border-radius:4px;
  box-shadow:0 0 0 1px #111;text-align:center;line-height:46px;font-size:13px;color:#f0f0f0}
.site-footer::before{content:"";position:absolute;inset:2px;border:1px solid #ddd;border-radius:3px}
.site-footer strong{color:var(--cream)}
</style>
</head>
<body>
<header class="brand">
  <span class="brand-mark"></span>
  <span class="brand-name">Chef Wen Chinese Restaurant</span>
</header>

<nav class="main-nav">
  <span class="nav-flourish left" role="img" aria-label="Decorative red and white swirl ornament"></span>
  <ul class="nav-links">
    <li class="active" style="left:122px">Home</li>
    <li style="left:219px">About</li>
    <li style="left:320px">Menu</li>
    <li style="left:413px">Winelist</li>
    <li style="left:532px">Facilities</li>
    <li style="left:656px">Events</li>
    <li style="left:763px">Contact</li>
  </ul>
  <span class="nav-flourish right" role="img" aria-label="Decorative red and white swirl ornament"></span>
</nav>

<section class="hero" role="img" aria-label="Photo of red, white and rosé wine glasses beside a plate of sweet and sour Chinese dish">
  <span class="hero-arrow prev"><svg width="14" height="28" viewBox="0 0 14 28"><path d="M12 2 L3 14 L12 26" fill="none" stroke="#fff" stroke-width="2"/></svg></span>
  <span class="hero-arrow next"><svg width="14" height="28" viewBox="0 0 14 28"><path d="M2 2 L11 14 L2 26" fill="none" stroke="#fff" stroke-width="2"/></svg></span>
</section>

<span class="divider-flourish" role="img" aria-label="Red swirl ornament divider"></span>

<section class="welcome">
  <h1><svg width="28" height="24" viewBox="0 0 28 24"><path d="M14 2 L27 13 H23 V23 H17 V16 H11 V23 H5 V13 H1 Z" fill="#fff6b8"/></svg>Welcome to &nbsp;Chef Wen</h1>
  <p class="one">Chef Wen is named after its’ executive chef, Mr. Wen. Chef Wen has been in his career for nearly two decades before he moved to Australia nine years ago. He settled in Adelaide then started his first restaurant, Lotus Court in Norwood. Lotus Court has been running successfully for years due to Chef Wen’s talent of cooking.</p>
  <p class="two">We offer an exceptional dining experience with authentic and dynamic dishes created with quality ingredients. The menu of Chef Wen is based on classic Cantonese dishes, featured by southern China’s local flavour characteristics. Taking advantage of South Australia’s rich and quality food resources...</p>
  <span class="read-more">READ MORE</span>
</section>

<section class="hours">
  <h2><svg width="23" height="23" viewBox="0 0 24 24"><circle cx="12" cy="12" r="10" fill="none" stroke="#fff" stroke-width="3"/><path d="M12 6 V12 H8" fill="none" stroke="#fff" stroke-width="2.5"/></svg>Opening Hours</h2>
  <p class="tagline">We are open 7 days</p>
  <dl>
    <dt>Lunch :</dt>
    <dd>Monday to Friday 11:30am – 2:30pm</dd>
    <dd class="gap">Saturday to Sunday 11:00am – 3:00pm</dd>
    <dt>Dinner :</dt>
    <dd>Monday to Sunday 6:00pm Until Late</dd>
  </dl>
</section>

<section class="wine-band">
  <div class="wine-photo" role="img" aria-label="Photo of red and white wine splashing from two glasses"></div>
  <ul class="wine-col" style="left:300px">
    <h3>WINES</h3>
    <li>Champagne</li><li>Sparkling White</li><li>Sparkling Red</li>
  </ul>
  <span class="wine-rule" style="left:423px"></span>
  <ul class="wine-col" style="left:447px">
    <h3>WHITE WINE</h3>
    <li>Riesling</li><li>Pinot Gris / Pinot Grigio</li><li>Sauvignon Blanc and Blends</li><li>Chardonnay</li><li>Other White Varietals</li>
  </ul>
  <span class="wine-rule" style="left:697px"></span>
  <ul class="wine-col red" style="left:719px">
    <h3>RED WINE</h3>
    <li>Rosé</li><li>Pinot Noir</li><li>Grenache/Sangiovese/Merlot</li><li>Cabernet Sauvignon &amp; Blends</li><li>Shiraz and Blends</li><li>Other Red Varietals</li>
  </ul>
</section>

<footer class="site-footer">© <strong>Chef Wen</strong> - 2014. All Rights Reserved.</footer>
</body>
</html>
```